Plakat-Design für Softwareentwicklung im Automotive-Sektor
Zielgruppe
Softwareentwicklung im Automotive-Sektor
Aufgabenstellung
Guten Tag,
wir benötigen ein Design für die Standwände und die Infotheke (LED-beleuchtet) unseres Messestandes auf einer Automotive Fachmesse.
Druckdaten, ein Layout unseres Standes und alle weiteren nötigen Daten finden Sie im Upload.
Im Upload finden Sie auch unser Signature Bild, das in das Design eingearbeitet werden soll - beispielsweise auf der Rückwand und die Seitenwände werden mit Logo/Slogan/einfarbig passend gestaltet oder Sie binden das Bild ganz ein - wir sind offen und gespannt auf Ihre Vorschläge!)
Außerdem finden Sie im Upload unser Firmenlogo samt Slogan 'Shape precise Systems.'
Unsere Website, um einen Eindruck vom Corporate Design zu erhalten:
https://www.quellorbit.de/de/
Wir freuen uns auf Ihre Designs!

```html
<!DOCTYPE html>
<html lang="de">
<head>
<meta charset="utf-8">
<title>QuellOrbit – Messestand Grafiken</title>
<link rel="stylesheet" href="https://fonts.googleapis.com/css2?family=Open+Sans:wght@400&family=Oswald:wght@400&family=Montserrat:wght@400;700&display=swap">
<style>
  :root {
    --bg: #7c7c7c;
    --white: #ffffff;
    --dark: #474747;
    --ink: #3a3a3a;
    --teal: #1f8f80;
    --muted: #8a8a8a;
    --photo-a: #1c1c1c;
    --photo-b: #4a4a4a;
  }
  * { box-sizing: border-box; margin: 0; padding: 0; }
  html, body { width: 1200px; height: 3839px; overflow: hidden; }
  body { background: var(--bg); position: relative; font-family: "Open Sans", sans-serif; }

  .panel { position: absolute; background: var(--white); overflow: hidden; }
  .panel.rule-teal { border-top: 6px solid var(--teal); }
  .panel.rule-dark { border-top: 6px solid var(--dark); }

  .brand { position: absolute; left: 0; right: 0; text-align: center; }
  .brand-name { display: inline-flex; align-items: center; gap: 10px; font-family: "Open Sans", sans-serif; font-weight: 400; color: var(--ink); letter-spacing: -0.5px; }
  .brand-name.teal { color: var(--teal); }
  .brand-dot { display: inline-block; border-radius: 50%; background: var(--dark); }
  .tagline { display: block; font-size: 14px; color: var(--muted); margin-top: -4px; }

  .photo { position: absolute; background:
      radial-gradient(ellipse 18% 70% at 60% 55%, rgba(184,104,42,.55), transparent 70%),
      linear-gradient(170deg, var(--photo-b), var(--photo-a) 60%, #111); }

  .url { position: absolute; left: 0; right: 0; text-align: center; font-family: "Oswald", sans-serif; color: var(--ink); }

  .band { position: absolute; left: 0; right: 0; background: var(--dark); }

  .mark { position: absolute; border-radius: 50%; background: var(--dark); display: flex; align-items: center; justify-content: center; }
  .mark-url { font-family: "Oswald", sans-serif; color: var(--white); font-size: 30px; }

  .slogan { position: absolute; font-family: "Oswald", sans-serif; text-transform: uppercase; line-height: 1.5; }
  .slogan-box { position: absolute; background: rgba(70,70,70,.85); }

  .services { position: absolute; left: 0; right: 0; text-align: center; font-family: "Montserrat", sans-serif; font-size: 16px; line-height: 21px; color: var(--ink); text-transform: uppercase; }
  .services b { font-weight: 700; }

  .strip-text { position: absolute; left: 50%; top: 40px; transform-origin: 0 0; transform: rotate(90deg) translateY(-50%); white-space: nowrap; font-family: "Open Sans", sans-serif; font-size: 52px; display: flex; align-items: center; gap: 22px; }
</style>
</head>
<body>

<!-- Row 1 -->
<section class="panel rule-teal" style="left:31px;top:25px;width:359px;height:895px;">
  <div class="brand" style="top:22px;"><span class="brand-name teal" style="font-size:46px;">QuellOrbit <i class="brand-dot" style="width:30px;height:30px;"></i></span><span class="tagline">Shape precise Systems.</span></div>
  <div class="photo" role="img" aria-label="Nachtaufnahme eines Autobahnkreuzes mit orangefarbenen Lichtspuren" style="left:0;top:114px;width:100%;height:627px;"></div>
  <div class="url" style="top:770px;font-size:28px;">www.quellorbit.de</div>
</section>

<section class="panel rule-teal" style="left:417px;top:25px;width:359px;height:895px;">
  <div class="brand" style="top:22px;"><span class="brand-name teal" style="font-size:46px;">QuellOrbit <i class="brand-dot" style="width:30px;height:30px;"></i></span><span class="tagline">Shape precise Systems.</span></div>
  <div class="photo" role="img" aria-label="Nachtaufnahme eines Autobahnkreuzes mit orangefarbenen Lichtspuren" style="left:0;top:114px;width:100%;height:627px;"></div>
  <div class="url" style="top:770px;font-size:28px;">www.quellorbit.de</div>
</section>

<section class="panel" style="left:809px;top:25px;width:360px;height:895px;">
  <div class="brand" style="top:28px;"><span class="brand-name" style="font-size:46px;">QuellOrbit <i class="brand-dot" style="width:30px;height:30px;"></i></span><span class="tagline">Shape precise Systems.</span></div>
  <div class="band" style="top:114px;height:8px;"></div>
  <div class="mark" style="left:55px;top:300px;width:250px;height:250px;"><span class="mark-url">www.quellorbit.de</span></div>
</section>

<!-- Row 2 -->
<section class="panel rule-dark" style="left:31px;top:972px;width:359px;height:899px;">
  <div class="url" style="top:40px;font-size:38px;">www.quellorbit.de</div>
  <div class="photo" role="img" aria-label="Nachtaufnahme eines Autobahnkreuzes mit orangefarbenen Lichtspuren" style="left:0;top:118px;width:100%;height:626px;"></div>
</section>

<section class="panel rule-teal" style="left:417px;top:972px;width:359px;height:899px;">
  <div class="brand" style="top:22px;"><span class="brand-name teal" style="font-size:46px;">QuellOrbit <i class="brand-dot" style="width:30px;height:30px;"></i></span><span class="tagline">Shape precise Systems.</span></div>
  <div class="photo" role="img" aria-label="Nachtaufnahme eines Autobahnkreuzes mit orangefarbenen Lichtspuren" style="left:0;top:118px;width:100%;height:626px;"></div>
  <div class="slogan-box" style="left:27px;top:274px;width:304px;height:321px;"></div>
  <div class="slogan" style="left:55px;top:300px;font-size:52px;color:var(--white);line-height:82px;">Shape<br>Precise<br>Systems</div>
</section>

<section class="panel" style="left:809px;top:972px;width:360px;height:899px;">
  <div class="brand" style="top:28px;"><span class="brand-name" style="font-size:46px;">QuellOrbit <i class="brand-dot" style="width:30px;height:30px;"></i></span><span class="tagline">Shape precise Systems.</span></div>
  <div class="band" style="top:118px;height:8px;"></div>
  <div class="services" style="top:220px;">
    Application <b>System Design</b><br>Hardware Development<br><b>Simulation Quality Management</b><br><b style="font-size:19px;">Software Development</b><br>Requirement Engineering<br><b>Integration</b> Proeject Management<br><b>Validation / Verification</b><br><b>Embedded Systems</b>
  </div>
  <div class="mark" style="left:60px;top:420px;width:240px;height:240px;"></div>
</section>

<!-- Row 3 -->
<section class="panel rule-teal" style="left:158px;top:1908px;width:462px;height:435px;">
  <div class="brand" style="top:10px;"><span class="brand-name teal" style="font-size:38px;">QuellOrbit <i class="brand-dot" style="width:24px;height:24px;"></i></span><span class="tagline" style="font-size:12px;">Shape precise Systems.</span></div>
  <div class="band" style="top:76px;height:5px;"></div>
  <svg style="position:absolute;left:0;top:81px;" width="462" height="354" viewBox="0 0 462 354" role="img" aria-label="Nachtaufnahme eines Autobahnkreuzes mit Lichtspuren, rechts rund beschnitten">
    <defs><linearGradient id="road" x1="0" y1="0" x2="1" y2="1"><stop offset="0" stop-color="#4a4a4a"/><stop offset=".5" stop-color="#2a2a2a"/><stop offset="1" stop-color="#151515"/></linearGradient></defs>
    <path d="M0 0 H300 A260 260 0 0 0 200 354 H0 Z" fill="url(#road)"/>
  </svg>
  <div class="slogan" style="left:312px;top:100px;font-size:30px;color:var(--ink);line-height:44px;">Shape<br>Precise<br>Systems</div>
  <div class="mark" style="left:310px;top:262px;width:130px;height:130px;"></div>
</section>

<section class="panel" style="left:158px;top:2366px;width:462px;height:432px;">
  <div class="brand" style="top:12px;"><span class="brand-name" style="font-size:32px;">QuellOrbit <i class="brand-dot" style="width:20px;height:20px;"></i></span><span class="tagline" style="font-size:11px;">Shape precise Systems.</span></div>
  <div class="band" style="top:72px;height:5px;"></div>
  <div class="slogan" style="left:80px;top:155px;font-size:30px;color:var(--ink);line-height:44px;">Shape<br>Precise<br>Systems</div>
  <div class="mark" style="left:232px;top:150px;width:150px;height:150px;"></div>
</section>

<section class="panel" style="left:651px;top:1901px;width:79px;height:897px;">
  <div class="strip-text" style="color:var(--ink);">QuellOrbit <i class="brand-dot" style="width:30px;height:30px;"></i></div>
</section>

<section class="panel" style="left:750px;top:1901px;width:79px;height:897px;background:var(--dark);">
  <div class="strip-text" style="color:var(--white);">QuellOrbit <i class="brand-dot" style="width:30px;height:30px;background:var(--white);"></i></div>
</section>

<section class="panel" style="left:848px;top:2422px;width:192px;height:376px;">
  <div class="brand" style="top:10px;"><span class="brand-name" style="font-size:24px;">QuellOrbit <i class="brand-dot" style="width:14px;height:14px;"></i></span><span class="tagline" style="font-size:8px;margin-top:0;">Shape precise Systems.</span></div>
  <div class="band" style="top:70px;height:4px;"></div>
  <div class="mark" style="left:56px;top:108px;width:80px;height:80px;"></div>
  <div class="brand" style="top:212px;font-size:38px;line-height:40px;color:var(--ink);">Quell<br>Orbit</div>
  <div class="band" style="top:303px;height:4px;"></div>
</section>

</body>
</html>
```